TALMORK

The business want a professional looking business card. We have a scetch we will add but want the extra upgrade, and would like more suggestions for variations of our business cards.

```html
<!DOCTYPE html>
<html lang="en">
<head>
<meta charset="utf-8">
<title>TALMORK Business Cards</title>
<link rel="stylesheet" href="https://fonts.googleapis.com/css2?family=Cinzel:wght@400;600&family=Josefin+Sans:wght@400&family=Montserrat:wght@500;600;700&display=swap">
<style>
  :root {
    --backdrop: #5b5b5e;
    --card-black: #0e0e0f;
    --pattern-dark: #141415;
    --pattern-light: #4a4a4c;
    --gold: #c9a24a;
    --gold-deep: #a88334;
    --cream: #ebe5d6;
    --gold-mid: #cdb06a;
    --bronze: #6e4c1e;
    --ink: #151310;
  }
  * { margin: 0; padding: 0; box-sizing: border-box; }
  html, body { width: 900px; height: 1200px; overflow: hidden; }
  body { background: var(--backdrop); position: relative; font-family: "Montserrat", sans-serif; }

  .card {
    position: absolute;
    left: 135px;
    width: 631px;
    height: 358px;
    border-radius: 14px;
    overflow: hidden;
  }
  .card--front { top: 215px; background: var(--card-black); }
  .card--back {
    top: 630px;
    background: linear-gradient(90deg, var(--cream) 0%, var(--gold-mid) 45%, #b8924a 70%, var(--bronze) 100%);
  }

  .pattern-field {
    position: absolute; inset: 0;
    background: linear-gradient(90deg, var(--pattern-dark) 0%, #1c1c1d 40%, var(--pattern-light) 100%);
  }

  .brand-mark { position: absolute; text-align: center; color: var(--gold); }
  .brand-mark__dot { display: block; margin: 0 auto; border-radius: 50%; background: var(--gold); }
  .brand-mark__name { font-family: "Cinzel", serif; font-weight: 400; line-height: 1; }
  .brand-mark__since { font-family: "Cinzel", serif; font-weight: 600; line-height: 1; }

  .card--front .brand-mark { left: 0; right: 0; top: 150px; }
  .card--front .brand-mark__dot { width: 40px; height: 40px; margin-bottom: 32px; }
  .card--front .brand-mark__name { font-size: 42px; letter-spacing: 14px; padding-left: 14px; }
  .card--front .brand-mark__since { font-size: 13px; letter-spacing: 6px; padding-left: 6px; margin-top: 14px; color: #d6b766; }

  .card--back .brand-mark { left: 376px; width: 200px; top: 124px; }
  .card--back .brand-mark__dot { width: 42px; height: 42px; margin-bottom: 30px; }
  .card--back .brand-mark__name { font-size: 29px; letter-spacing: 8px; padding-left: 8px; color: var(--gold); }
  .card--back .brand-mark__since { font-size: 9px; letter-spacing: 4px; padding-left: 4px; margin-top: 6px; color: var(--gold-deep); }

  .holder { position: absolute; left: 49px; top: 64px; }
  .holder__company { font-family: "Josefin Sans", sans-serif; font-size: 30px; color: var(--gold-deep); letter-spacing: -0.5px; line-height: 1; }
  .holder__role { font-size: 22px; font-weight: 500; color: var(--ink); margin-top: 14px; line-height: 1; }
  .holder__name { font-size: 21px; font-weight: 700; color: var(--gold-deep); margin-top: 12px; line-height: 1; }

  .contact { position: absolute; left: 49px; top: 220px; list-style: none; }
  .contact__item { display: flex; align-items: center; gap: 6px; font-size: 18px; font-weight: 600; color: var(--ink); height: 30px; }
  .contact__icon { width: 12px; height: 12px; flex: none; }
</style>
</head>
<body>
  <section class="card card--front" aria-label="Business card front">
    <div class="pattern-field" role="img" aria-label="Repeating embossed ornamental flower pattern on black"></div>
    <div class="brand-mark">
      <span class="brand-mark__dot"></span>
      <div class="brand-mark__name">TALMORK</div>
      <div class="brand-mark__since">SINCE 2026</div>
    </div>
  </section>

  <section class="card card--back" aria-label="Business card back">
    <div class="holder">
      <div class="holder__company">TALMORK H MORVIK</div>
      <div class="holder__role">CEO &amp; Founder</div>
      <div class="holder__name">Henrik Aas Morvik</div>
    </div>
    <ul class="contact">
      <li class="contact__item">
        <svg class="contact__icon" viewBox="0 0 12 12"><rect x="3" y="0.5" width="6" height="11" rx="1" fill="none" stroke="#151310" stroke-width="1.2"/><line x1="5" y1="9.6" x2="7" y2="9.6" stroke="#151310" stroke-width="1"/></svg>
        004790412738
      </li>
      <li class="contact__item">
        <svg class="contact__icon" viewBox="0 0 12 12"><rect x="0.5" y="2.5" width="11" height="7" fill="none" stroke="#151310" stroke-width="1.2"/><polyline points="0.5,2.5 6,6.5 11.5,2.5" fill="none" stroke="#151310" stroke-width="1.2"/></svg>
        talmork.llc@mailbox.com
      </li>
      <li class="contact__item">
        <svg class="contact__icon" viewBox="0 0 12 12"><circle cx="6" cy="6" r="5" fill="none" stroke="#151310" stroke-width="1.1"/><ellipse cx="6" cy="6" rx="2.2" ry="5" fill="none" stroke="#151310" stroke-width="0.9"/><line x1="1" y1="6" x2="11" y2="6" stroke="#151310" stroke-width="0.9"/></svg>
        www.talmork.llc
      </li>
    </ul>
    <div class="brand-mark">
      <span class="brand-mark__dot"></span>
      <div class="brand-mark__name">TALMORK</div>
      <div class="brand-mark__since">SINCE 2026</div>
    </div>
  </section>
</body>
</html>
```